Lo Mara Menu Design Project

This project is pretty straight forward. You will be given 3 files which include the following:
1. Our proposed menu
2. Our Company logo
3. A sample menu on what we are looking for design wise

Your job is to create a visually pleasing menu that is simple, clean and fresh. Please refer to our home website for additional information. (www.lomara-eats.com) Must be in eps or equivalent format.

Target Market(s)

20s to 40s

Industry/Entity Type

It Company

Requirements
Must have
• Company log
Must be in EPS format

```html
<!DOCTYPE html>
<html lang="en">
<head>
<meta charset="utf-8">
<title>Lo Mara — Salads &amp; Chicken Menu</title>
<link rel="stylesheet" href="https://fonts.googleapis.com/css2?family=Josefin+Sans:ital,wght@0,400;0,600;1,300&display=swap">
<style>
  :root {
    --ink: #000000;
    --cream: #f1ede6;
    --red: #c8202a;
    --gold: #b98a2c;
    --gold-deep: #6e4f14;
    --ember: #a8321f;
    --ember-deep: #5c1a10;
  }
  * { box-sizing: border-box; margin: 0; padding: 0; }
  html, body { width: 1200px; height: 1000px; overflow: hidden; background: var(--ink); }
  body { font-family: "Josefin Sans", sans-serif; color: var(--cream); }

  .menu { position: relative; width: 1200px; height: 1000px; overflow: hidden; background: var(--ink); }

  .backdrop { position: absolute; inset: 0; }
  .backdrop-top {
    position: absolute; left: 0; top: 0; width: 1200px; height: 300px;
    background: linear-gradient(180deg, var(--gold) 0%, rgba(110,79,20,0.55) 12%, rgba(0,0,0,0) 100%);
    opacity: 0.75;
  }
  .backdrop-bottom {
    position: absolute; left: 0; bottom: 0; width: 1200px; height: 580px;
    background: linear-gradient(0deg, var(--ember) 0%, rgba(92,26,16,0.6) 40%, rgba(0,0,0,0) 100%);
    opacity: 0.7;
  }

  .section-title {
    position: absolute; left: 0; width: 1200px; text-align: center;
    color: var(--red); font-weight: 400; font-size: 22px; letter-spacing: 0.5px;
  }
  .section-title.salads { top: 53px; }
  .section-title.chicken { top: 290px; }

  .note { font-style: italic; font-weight: 300; font-size: 19px; line-height: 25px; text-align: center; }
  .salads-note { position: absolute; top: 81px; left: 0; width: 1200px; }
  .chicken-note { position: absolute; top: 310px; left: 46px; width: 510px; }

  .salad { position: absolute; top: 130px; width: 360px; text-align: center; }
  .salad-1 { left: 42px; }
  .salad-2 { left: 432px; }
  .salad-3 { left: 796px; }
  .salad-name { font-weight: 600; font-size: 20px; line-height: 25px; letter-spacing: 0.3px; }
  .salad-name .price { margin-left: 14px; }
  .desc { font-style: italic; font-weight: 300; font-size: 19px; line-height: 25px; }

  .rule { position: absolute; background: var(--red); }
  .rule-horizontal { left: 48px; top: 269px; width: 1104px; height: 3px; }
  .rule-vertical { left: 604px; top: 352px; width: 2px; height: 648px; }

  .dish-list { position: absolute; }
  .dish-list.left { left: 46px; top: 434px; width: 510px; }
  .dish-list.right { left: 658px; top: 314px; width: 494px; }
  .dish-head { display: flex; justify-content: space-between; font-weight: 600; font-size: 19px; line-height: 25px; letter-spacing: 0.3px; }
  .dish .desc { padding-left: 37px; }
  .dish .desc.flush { padding-left: 0; }

  .brand-tag {
    position: absolute; bottom: 36px; color: var(--red);
    font-weight: 600; font-size: 16px; line-height: 18px; text-align: center; width: 80px;
  }
  .brand-tag.left { left: 6px; }
  .brand-tag.right { right: 6px; }
</style>
</head>
<body>
<main class="menu">
  <div class="backdrop" role="img" aria-label="Decorative geometric pattern in gold at the top fading to red at the bottom">
    <div class="backdrop-top"></div>
    <div class="backdrop-bottom"></div>
  </div>

  <h2 class="section-title salads">SALADS</h2>
  <p class="note salads-note">Can replace Chicken with Tofu for $1.50</p>

  <article class="salad salad-1">
    <h3 class="salad-name">Chinese Chicken Salad<span class="price">10.50</span></h3>
    <p class="desc">Shredded lettuce, chicken breast,<br>carrots, toasted almonds,<br>browncrunchies, and white crunchies<br>with tart red ginger dressing</p>
  </article>
  <article class="salad salad-2">
    <h3 class="salad-name">Main Mein Salad<span class="price">9.95</span></h3>
    <p class="desc">Cold lo mein noodles with chicken<br>breast and vegetables in a spicy<br>peanut dressing.</p>
  </article>
  <article class="salad salad-3">
    <h3 class="salad-name">Sesame Chicken Salad<span class="price">9.95</span></h3>
    <p class="desc">Shredded lettuce, chicken scallions,<br>breast, red cabbage, carrots,<br>browncrunchies, fresh oranges,<br>scallions, and sesame dressing.</p>
  </article>

  <div class="rule rule-horizontal"></div>
  <h2 class="section-title chicken">CHICKEN</h2>
  <div class="rule rule-vertical"></div>

  <p class="note chicken-note">For white meat chicken, add $1.00.<br>Enjoy a Half Chinese Chicken Salad or Plain Fried<br>Rice with any entrée for $5.50<br>Can replace Chicken with Tofu for $1.50</p>

  <section class="dish-list left">
    <div class="dish"><div class="dish-head"><span>Orange Chicken</span><span>11.95</span></div>
      <p class="desc">Crispy chicken breast with onions and red and<br>green bell peppers in a tangy orange sauce.</p></div>
    <div class="dish"><div class="dish-head"><span>General Tso's Chicken</span><span>11.75</span></div>
      <p class="desc">Crispy dark meat chicken with chili peppers in a<br>spicy tangerine sauce topped with scallions.</p></div>
    <div class="dish"><div class="dish-head"><span>Kung Pao Chicken</span><span>11.95</span></div>
      <p class="desc">Dark meat chicken with red bell peppers, peanuts,<br>and water chestnuts in spicy red sauce.</p></div>
    <div class="dish"><div class="dish-head"><span>Chicken Lettuce Cups</span><span>11.75</span></div>
      <p class="desc">Minced white meat chicken with bell peppers,<br>water chestnuts, black mushrooms, pine nuts, and<br>white crunchies. Served with four lettuce cups.</p></div>
    <div class="dish"><div class="dish-head"><span>Chicken With Asparagus</span><span>11.95</span></div>
      <p class="desc">Chicken breast with asparagus and carrots in a<br>lemon white wine sauce.</p></div>
    <div class="dish"><div class="dish-head"><span>Chicken With Snow Peas</span><span>11.75</span></div>
      <p class="desc flush">Chicken breast served with snow peas, fresh<br>mushrooms, carrots, and sliced garlic.</p></div>
  </section>

  <section class="dish-list right">
    <div class="dish"><div class="dish-head"><span>Teriyaki Chicken Bowl</span><span>11.95</span></div>
      <p class="desc">Dark meat chicken glazed in Teriyaki sauce<br>placed over a bed of rice.</p></div>
    <div class="dish"><div class="dish-head"><span>Tangerine Chicken</span><span>11.75</span></div>
      <p class="desc">Crispy chicken breast topped with scallions in a<br>tangerine sauce.</p></div>
    <div class="dish"><div class="dish-head"><span>Almond Chicken</span><span>11.95</span></div>
      <p class="desc">Dark meat chicken with bamboo shoots, celery,<br>water chestnuts, and toasted almonds.<br>Prepared regularly or mandarin-Style.</p></div>
    <div class="dish"><div class="dish-head"><span>Lemon Chicken</span><span>11.75</span></div>
      <p class="desc">Crispy chicken breast marinated in garlic and<br>ginger; served with a tart lemon sauce on the<br>side.</p></div>
    <div class="dish"><div class="dish-head"><span>Cashew Chicken</span><span>11.95</span></div>
      <p class="desc">Chicken breast, zucchini, onions, garlic, ginger,<br>and cashews tossed in an oyster sauce.</p></div>
    <div class="dish"><div class="dish-head"><span>Curry Chicken</span><span>11.95</span></div>
      <p class="desc">Chicken breast with potatoes, onions, green<br>peas, and carrots in a curry sauce.</p></div>
    <div class="dish"><div class="dish-head"><span>Sweet And Sour Chicken</span><span>11.50</span></div>
      <p class="desc">Crispy chicken breast, bell peppers, onions, and<br>pineapple in a sweet and sour sauce.</p></div>
  </section>

  <div class="brand-tag left">Lo Mara</div>
  <div class="brand-tag right">Lo Mara</div>
</main>
</body>
</html>
```